Larkmoor Drones Business Card

We are a new company based in Central Queensland, Australia that uses specalised drones (Voskel Ferra Q80) to undertake mainly agricultural operations, like spraying weeds, spraying crops, spreading seed etc. I have attached a Plimbo proof of a card I was thinking along the lines of - purely a start point. The drone used in the business card MUST be a Voskel Ferra Q80.
I am very open to other ideas, especially fonts and layout. I don't have website etc set up yet.
The images are stock and easily interchangeable, I just ask that any background images reflect the local central Queensland area. The photo of the drone is not even complete (propellers cut off) and I need a new stock photo – I’m not sure if this is an issue, or I can pay for an image if need be. PLEASE FIND AN FERRA Q80 image - 4 sprayers, not 6.
The logo/business name is very draft and looking for further ideas, ideally incorporating drones or agriculture design elements into the design of the business name. The business name needs work on the graphic/design – it is a draft that I have included, the drone propellers (being a different colour) are DRAFT only and intended for changes. PLEASE DO NOT USE THE DRONE PORPELLER I HAVE USED AS A DRAFT. TRY TO FIND SOMETHING ELSE.. The arrow is a shape and not aligned in any way, I would also like ideas on different fonts and additional elements, like air streams, aviation elements, aviation or country western (farming like) themes and fonts etc.
Ideally looking at staying within the blue, green and yellow colours, keeping with an natural, outdoorsy, environmental feel.

Target Market(s)

Farmers, Agriculture, Local Governments, Land Managers

Industry/Entity Type

Agriculture, Drones, Aviation

Contact Information for Business Card

Agricultural Drone (Voskel Ferra Q80), Farming, Business Name.

Font styles to use
Sans Serif

Colors
0054AA
0677BA
7BADD7
CADEEF
E8F1F8
0094D4
00A9DD
6FCCEA
C7EBF8
E9F6FB
00AB8E
00BBA5
67D7C9
C6EFE9
E9F9F6
59FF00
82FF00
B8FF75
E3FFCB
F4FFEA

Requirements
Must have
• Voskel Ferra Q80 Drone
Should not have
• Tractors

```html
<!DOCTYPE html>
<html lang="en">
<head>
<meta charset="utf-8">
<title>Larkmoor Drones – Business Card</title>
<link rel="stylesheet" href="https://fonts.googleapis.com/css2?family=Alfa+Slab+One&family=Roboto+Slab:wght@700&family=Playfair+Display:wght@400&display=swap">
<style>
  :root{
    --stage:#232323;
    --slate-blue:#4a5a78;
    --field-green:#7f963c;
    --copper:#e3a373;
    --ink-blue:#3d5a8a;
    --drone-tone:#4a4238;
    --white:#ffffff;
  }
  *{margin:0;padding:0;box-sizing:border-box}
  html,body{width:1200px;height:800px;overflow:hidden;background:var(--stage)}
  .sheet{position:relative;width:1200px;height:800px}
  .card{position:absolute;top:245px;width:540px;height:309px;border-radius:24px;overflow:hidden;box-shadow:0 14px 30px rgba(0,0,0,.55)}
  .card--front{left:40px}
  .card--back{left:620px}
  .card svg{display:block;width:540px;height:309px}
  .services{font-family:"Alfa Slab One",serif;fill:var(--ink-blue);font-size:21px;letter-spacing:3px}
  .brand-name{font-family:"Alfa Slab One",serif;fill:var(--white)}
  .region{font-family:"Playfair Display",serif;fill:var(--white);font-size:12px;letter-spacing:1.6px}
  .contact{font-family:"Roboto Slab",serif;font-weight:700;fill:var(--white);font-size:12px}
  .icon-ring{fill:none;stroke:var(--white);stroke-width:1.6}
  .icon-line{fill:none;stroke:var(--white);stroke-width:1.3;stroke-linecap:round;stroke-linejoin:round}
</style>
</head>
<body>
<main class="sheet">

  <section class="card card--front" aria-label="Larkmoor Drones card front">
    <svg viewBox="0 0 540 309" xmlns="http://www.w3.org/2000/svg">
      <defs>
        <linearGradient id="sunsetField" x1="0" y1="0" x2="0" y2="1">
          <stop offset="0" stop-color="#e58a45"/>
          <stop offset=".28" stop-color="#f3c66a"/>
          <stop offset=".55" stop-color="#c9b86a"/>
          <stop offset=".8" stop-color="#8f9d45"/>
          <stop offset="1" stop-color="#6e8431"/>
        </linearGradient>
        <radialGradient id="droneFront" cx=".5" cy=".5" r=".5">
          <stop offset="0" stop-color="#4a4238" stop-opacity=".85"/>
          <stop offset=".6" stop-color="#6b5a45" stop-opacity=".5"/>
          <stop offset="1" stop-color="#e9d7a8" stop-opacity="0"/>
        </radialGradient>
      </defs>
      <rect class="field-photo" role="img" aria-label="Central Queensland crop field under a sunset sky" x="0" y="0" width="540" height="260" fill="url(#sunsetField)"/>
      <ellipse class="drone-photo" role="img" aria-label="Voskel Ferra Q80 spray drone with four sprayers misting the crop" cx="225" cy="105" rx="150" ry="52" fill="url(#droneFront)"/>
      <text class="services" x="270" y="42" text-anchor="middle">SPRAY · WEED · SEED · FEED</text>
      <polygon class="band band--blue" points="0,165 540,122 540,168 0,255" fill="var(--slate-blue)"/>
      <polygon class="band band--green" points="0,255 540,168 540,309 0,309" fill="var(--field-green)"/>
      <text class="brand-name" x="300" y="206" font-size="36" text-anchor="middle">LARKMOOR</text>
      <text class="brand-name" x="330" y="246" font-size="36" text-anchor="middle">DRONES</text>
      <text class="region" x="320" y="276" text-anchor="middle">SERVICING CENTRAL QUEENSLAND</text>
    </svg>
  </section>

  <section class="card card--back" aria-label="Larkmoor Drones card back">
    <svg viewBox="0 0 540 309" xmlns="http://www.w3.org/2000/svg">
      <defs>
        <linearGradient id="backPhoto" x1="1" y1="0" x2="0" y2="1">
          <stop offset="0" stop-color="#f0a24c"/>
          <stop offset=".25" stop-color="#f5cf78"/>
          <stop offset=".55" stop-color="#b6b466"/>
          <stop offset="1" stop-color="#7a9036"/>
        </linearGradient>
        <linearGradient id="greenFade" x1="0" y1="0" x2="0" y2="1">
          <stop offset="0" stop-color="#7f963c" stop-opacity="0"/>
          <stop offset=".55" stop-color="#7f963c" stop-opacity=".7"/>
          <stop offset="1" stop-color="#7f963c"/>
        </linearGradient>
        <linearGradient id="blueWave" x1="0" y1="0" x2="1" y2="0">
          <stop offset="0" stop-color="#4a5a78"/>
          <stop offset=".6" stop-color="#4a5a78"/>
          <stop offset="1" stop-color="#5d7a5c"/>
        </linearGradient>
        <radialGradient id="droneBack" cx=".5" cy=".5" r=".5">
          <stop offset="0" stop-color="#4a4238" stop-opacity=".85"/>
          <stop offset=".6" stop-color="#6b5a45" stop-opacity=".5"/>
          <stop offset="1" stop-color="#f5d890" stop-opacity="0"/>
        </radialGradient>
      </defs>
      <rect class="field-photo" role="img" aria-label="Green crop field under a golden Central Queensland sky" x="0" y="0" width="540" height="309" fill="url(#backPhoto)"/>
      <ellipse class="drone-photo" role="img" aria-label="Voskel Ferra Q80 spray drone with four sprayers in flight" cx="410" cy="75" rx="110" ry="45" fill="url(#droneBack)"/>
      <rect class="field-fade" x="0" y="120" width="540" height="189" fill="url(#greenFade)"/>
      <path class="wave wave--green" d="M0,140 C140,150 230,110 300,40 C330,12 360,6 390,10 L300,120 C250,180 160,200 0,209 Z" fill="var(--field-green)" opacity=".9"/>
      <path class="wave wave--blue" d="M0,0 H390 C330,8 300,40 270,80 C220,140 140,168 0,170 Z" fill="url(#blueWave)"/>
      <path class="wave-line wave-line--copper" d="M10,172 C150,168 225,140 275,80 C310,36 345,12 400,6" fill="none" stroke="var(--copper)" stroke-width="3"/>
      <path class="wave-ribbon" d="M280,135 C310,70 350,30 410,8 L400,18 C355,40 320,80 292,150 Z" fill="var(--slate-blue)"/>

      <g class="contact-list" text-anchor="end">
        <text class="contact" x="495" y="150">(07) 4900 3172</text>
        <text class="contact" x="495" y="172">www.larkmoorfly.com.au</text>
        <text class="contact" x="495" y="194">info@larkmoorfly.com.au</text>
        <text class="contact" x="495" y="216">@larkmoorfly</text>
        <text class="contact" x="495" y="238">@larkmoorfly</text>
      </g>
      <g class="contact-icons">
        <circle class="icon-ring" cx="512" cy="146" r="8"/>
        <path class="icon-line" d="M508.5,142.5 q0,6 7,7 l1,-2 -2,-1.5 -1.5,1.5 q-2,-1 -3,-3 l1.5,-1.5 -1.5,-2 z"/>
        <circle class="icon-ring" cx="512" cy="168" r="8"/>
        <ellipse class="icon-line" cx="512" cy="168" rx="3" ry="5"/>
        <path class="icon-line" d="M507,168 h10"/>
        <circle class="icon-ring" cx="512" cy="190" r="8"/>
        <rect class="icon-line" x="507.5" y="187" width="9" height="6.5"/>
        <path class="icon-line" d="M507.5,187 l4.5,3.5 4.5,-3.5"/>
        <circle class="icon-ring" cx="512" cy="212" r="8"/>
        <circle class="icon-ring" cx="512" cy="234" r="8"/>
      </g>

      <text class="brand-name" x="38" y="276" font-size="30">LARKMOOR DRONES</text>
      <text class="region" x="48" y="297">SERVICING CENTRAL QUEENSLAND</text>
    </svg>
  </section>

</main>
</body>
</html>
```